Brell Stone Company Business Cards

Front and Back Business Card - logo and text setup - cool design. I need workable photoshop or illustrator files so I can setup each employee card with design that is created
Updates

Hi everyone, thank you for the great entries. Please no more white and blue cards - there are so many already - black and silver only now please. thanks!

Target Market(s)

Construction Industry - Facility Managers

Industry/Entity Type

Construction

Contact Information for Business Card

I really like contemporary simplistic looks - clean neat....not opposed to seeing some black backrounds

Requirements
Must have
• Logo/website address with design on front only - www.brellstone-example.com (logo attached)
• Back:
• Name/Title/Company Address/Phone/email address
Nice to have
• Cool design
Should not have
• Nothing gimmicky like Fire or Water - since we are a Fire Protection company - it has all been done

```html
<!DOCTYPE html>
<html lang="en">
<head>
<meta charset="utf-8">
<title>Brell Stone Company Business Cards</title>
<link href="https://fonts.googleapis.com/css2?family=Lato:wght@400;700;900&display=swap" rel="stylesheet">
<style>
  :root {
    --black: #151617;
    --black-soft: #2a2c2f;
    --silver: #c3c7cc;
    --silver-light: #e6e8eb;
    --silver-dark: #8b9097;
    --rule: #b9bdc3;
    --stage: #dcdee1;
  }
  * { margin: 0; padding: 0; box-sizing: border-box; }
  html, body { width: 1200px; height: 896px; overflow: hidden; }
  body {
    background: var(--stage);
    font-family: "Lato", Arial, sans-serif;
    display: flex;
    flex-direction: column;
    align-items: center;
    justify-content: center;
    gap: 46px;
  }
  .card {
    width: 660px;
    height: 377px;
    position: relative;
    overflow: hidden;
    box-shadow: 0 6px 18px rgba(0,0,0,0.22);
  }
  /* Front */
  .card-front {
    background: var(--black);
    display: flex;
    flex-direction: column;
    align-items: center;
    justify-content: center;
    gap: 34px;
  }
  .wordmark {
    display: flex;
    align-items: center;
    gap: 14px;
    font-weight: 900;
    font-size: 58px;
    letter-spacing: -1px;
    line-height: 1;
  }
  .wordmark-mark { width: 20px; height: 20px; background: var(--silver); }
  .card-front .wordmark { color: var(--silver-light); }
  .front-web { color: var(--silver); font-size: 19px; letter-spacing: 0.3px; }
  /* Back */
  .card-back { background: var(--silver-light); border-bottom: 10px solid var(--black); }
  .identity { position: absolute; left: 48px; top: 64px; color: var(--black); }
  .person-name { font-size: 25px; font-weight: 700; letter-spacing: 0.6px; text-transform: uppercase; }
  .person-title { font-size: 18px; color: var(--black-soft); margin-top: 2px; }
  .contacts { list-style: none; margin-top: 16px; }
  .contacts li {
    display: flex; align-items: center; gap: 10px;
    font-size: 16px; color: var(--black-soft); margin-bottom: 5px;
  }
  .contacts svg { width: 14px; height: 14px; color: var(--black); flex: none; }
  .card-back .wordmark { position: absolute; right: 46px; top: 112px; color: var(--black); font-size: 50px; }
  .card-back .wordmark-mark { background: var(--silver-dark); }
  .rule { position: absolute; height: 1px; background: var(--rule); }
  .rule-top { left: 300px; right: 46px; top: 98px; }
  .rule-bottom { left: 48px; right: 46px; top: 252px; }
  .address {
    position: absolute; right: 46px; top: 270px;
    text-align: right; font-size: 17px; color: var(--black-soft); line-height: 1.35;
  }
</style>
</head>
<body>
  <section class="card card-front" aria-label="Business card front">
    <div class="wordmark"><span class="wordmark-mark"></span><span>Brell Stone</span></div>
    <p class="front-web">www.brellstone-example.com</p>
  </section>

  <section class="card card-back" aria-label="Business card back">
    <div class="identity">
      <h1 class="person-name">Daniel Marsh</h1>
      <p class="person-title">Managing Director</p>
      <ul class="contacts">
        <li><svg viewBox="0 0 16 16" aria-hidden="true"><path fill="currentColor" d="M4 1h2l1 4-2 1c1 2 3 4 5 5l1-2 4 1v2c0 1-1 3-3 3C6 15 1 10 1 4c0-2 2-3 3-3z"/></svg>044-555 018 234</li>
        <li><svg viewBox="0 0 16 16" aria-hidden="true"><path d="M1 3h14v10H1z M2 4l6 5 6-5" fill="none" stroke="currentColor" stroke-width="1.6"/></svg>info@brellstone-example.com</li>
        <li><svg viewBox="0 0 16 16" aria-hidden="true"><circle cx="8" cy="8" r="7" fill="currentColor"/><path d="M1 8h14M8 1c3 3 3 11 0 14M8 1c-3 3-3 11 0 14" stroke="#e6e8eb" stroke-width="1" fill="none"/></svg>www.brellstone-example.com</li>
      </ul>
    </div>
    <div class="rule rule-top"></div>
    <div class="wordmark"><span class="wordmark-mark"></span><span>Brell Stone</span></div>
    <div class="rule rule-bottom"></div>
    <p class="address">88, Quarry Lane<br>Stonebridge, 40217</p>
  </section>
</body>
</html>
```